Brightmoor Talent company

We require a website for job recruitment company called "Brightmoor Talent"
Our company is specialising in recruitment of skilled labour from Sri Lanka into Australian market.
We would like to include a job advertising plugin where jobs can be listed and applied for .
COPYWRITING MUST BE INCLUDED !

Industry/Entity Type

Recruitment

Coding

Coded - Design and coding required

Number of Pages Required

5+ page

Colors

Designer to choose colors to be used in the design.

```html
<!DOCTYPE html>
<html lang="en">
<head>
<meta charset="utf-8">
<title>Brightmoor Talent – Skilled Sri Lankan Workers for Australia</title>
<link href="https://fonts.googleapis.com/css2?family=Montserrat:wght@500;600;700&family=Poppins:wght@300;400;500;600&display=swap" rel="stylesheet">
<style>
:root{
  --blue:#1a63b4;
  --blue-bright:#2e8ff0;
  --navy:#0b2a57;
  --navy-deep:#0a2456;
  --ink:#2b2b2b;
  --muted:#3d3d3d;
  --card:#eef5fd;
  --band:#e2effc;
  --white:#ffffff;
}
*{box-sizing:border-box;margin:0;padding:0}
html,body{width:1200px;height:3747px;overflow:hidden}
body{position:relative;background:var(--white);font-family:"Poppins",sans-serif;color:var(--ink)}
.abs{position:absolute}
a{color:inherit;text-decoration:none}

/* header */
.site-header{position:absolute;left:0;top:0;width:1200px;height:124px;background:var(--white)}
.brand{position:absolute;left:73px;top:40px;font-family:"Poppins",sans-serif;font-weight:600;font-size:30px;color:var(--navy);display:flex;align-items:center;gap:10px}
.brand-dot{width:14px;height:14px;background:var(--blue);border-radius:50%}
.main-nav a{position:absolute;top:50px;font-size:16px;color:var(--ink)}
.btn{position:absolute;display:flex;align-items:center;justify-content:center;background:var(--blue);color:var(--white);font-family:"Montserrat",sans-serif;font-weight:700;font-size:16px;border-radius:30px}
.login-link{position:absolute;left:1075px;top:50px;font-size:16px;font-weight:500}

/* hero */
.hero{position:absolute;left:0;top:124px;width:1200px;height:549px;background:linear-gradient(120deg,#4a4c52 0%,#2f3136 45%,#3a3f46 75%,#6b7078 100%)}
.hero-title{position:absolute;left:0;width:1200px;top:160px;text-align:center;font-family:"Montserrat",sans-serif;font-weight:600;font-size:62px;color:var(--white)}
.hero-title span{color:var(--blue-bright);font-weight:700}
.hero-sub{position:absolute;left:0;width:1200px;top:244px;text-align:center;font-size:25px;line-height:44px;color:var(--white);font-weight:300}
.hero-arrow{position:absolute;top:296px;width:34px;height:34px;border-radius:50%;background:var(--white)}

/* search band */
.search-band{position:absolute;left:0;top:673px;width:1200px;height:108px;background:var(--blue)}
.search-box{position:absolute;left:250px;top:16px;width:710px;height:76px;background:var(--white);border-radius:38px;overflow:hidden}
.search-box .placeholder{position:absolute;left:34px;top:26px;font-size:16px;color:#a8a8a8}
.search-box .go{position:absolute;left:562px;top:0;width:148px;height:76px;background:var(--navy);color:var(--white);display:flex;align-items:center;justify-content:center;font-size:17px;font-weight:500}

.section-title{position:absolute;left:0;width:1200px;text-align:center;font-family:"Montserrat",sans-serif;font-weight:700;font-size:36px;color:var(--ink)}
.section-title span{color:var(--blue)}

.tab{position:absolute;top:925px;width:192px;height:51px;border-radius:8px;background:var(--blue);color:var(--white);font-family:"Montserrat",sans-serif;font-weight:700;font-size:18px;display:flex;align-items:center;justify-content:center}
.tab.active{background:var(--navy)}

.job-card{position:absolute;width:442px;height:117px;background:var(--card);border-left:6px solid var(--blue)}
.job-card.alt{border-left-color:var(--navy)}
.job-title{position:absolute;left:18px;top:16px;font-family:"Montserrat",sans-serif;font-weight:600;font-size:17px;color:var(--ink)}
.job-desc{position:absolute;left:16px;top:46px;width:290px;font-size:13.5px;line-height:25px;color:var(--muted)}
.apply{position:absolute;left:311px;top:46px;width:109px;height:30px;background:var(--blue);color:var(--white);font-family:"Montserrat",sans-serif;font-weight:700;font-size:14px;display:flex;align-items:center;justify-content:center}
.apply.dark{background:var(--navy)}

.page-no{position:absolute;top:1548px;width:28px;height:28px;border-radius:4px;background:var(--blue);color:var(--white);font-size:15px;font-weight:600;display:flex;align-items:center;justify-content:center}
.page-no.current{background:var(--navy)}

/* about */
.about-photo{position:absolute;left:134px;top:1660px;width:436px;height:436px;border-radius:50%;background:radial-gradient(circle at 40% 40%,#c9ccd0,#7c838b 70%,#4c535a)}
.about-ring{position:absolute;left:128px;top:1654px;width:448px;height:448px;border-radius:50%;border:3px solid #7ba4d3;border-left-color:var(--navy-deep);border-bottom-color:var(--navy-deep)}
.about-title{position:absolute;left:609px;top:1718px;font-family:"Montserrat",sans-serif;font-weight:700;font-size:36px}
.about-title span{color:var(--blue)}
.about-text{position:absolute;left:609px;top:1788px;width:452px;font-size:15.5px;line-height:25.7px;text-align:justify;color:var(--muted)}

/* how it works */
.how-band{position:absolute;left:0;top:2193px;width:1200px;height:760px;background:var(--band)}
.step-circle{position:absolute;width:150px;height:150px;border-radius:50%;background:var(--white);border:8px solid var(--navy-deep);box-shadow:-6px 8px 0 var(--blue)}
.step-circle svg{position:absolute;left:31px;top:31px}
.step-no{position:absolute;width:40px;height:40px;border-radius:50%;background:var(--navy-deep);border:3px solid var(--white);color:var(--white);font-family:"Montserrat",sans-serif;font-weight:700;font-size:17px;display:flex;align-items:center;justify-content:center}
.step-title{position:absolute;font-family:"Montserrat",sans-serif;font-weight:600;font-size:17px;color:var(--ink)}
.step-text{position:absolute;width:190px;font-size:16px;line-height:30px;color:var(--muted)}

/* testimonials */
.testimonial{position:absolute;left:138px;top:3095px;width:931px;height:277px;background:#f7f8fa;box-shadow:0 4px 18px rgba(0,0,0,.08)}
.client-photo{position:absolute;left:19px;top:36px;width:204px;height:204px;border-radius:50%;border:2px solid var(--blue);padding:10px;background:var(--white)}
.client-photo div{width:100%;height:100%;border-radius:50%;background:radial-gradient(circle at 50% 40%,#b07a55,#8a9c5c 70%,#d79a3a)}
.client-name{position:absolute;left:288px;top:60px;font-size:22px;color:var(--blue)}
.client-role{position:absolute;left:288px;top:100px;font-size:16px;font-weight:500}
.client-quote{position:absolute;left:288px;top:136px;width:630px;font-size:16px;line-height:30px}
.quote-mark{position:absolute;left:838px;top:200px}
.nav-circle{position:absolute;top:3218px;width:34px;height:34px;border-radius:50%;border:2px solid #bbb}
.nav-circle.right{border-color:var(--blue)}

/* footer */
.site-footer{position:absolute;left:0;top:3475px;width:1200px;height:272px;background:var(--navy-deep);color:var(--white)}
.social{position:absolute;top:62px;width:22px;height:22px;border-radius:50%;border:2px solid var(--blue)}
.rule{position:absolute;left:0;width:1200px;height:1px;background:rgba(255,255,255,.18)}
.footer-links{position:absolute;left:0;width:1200px;top:163px;text-align:center;font-size:17px;word-spacing:2px}
.footer-links span{margin:0 18px}
.copyright{position:absolute;left:0;width:1200px;top:238px;text-align:center;font-size:14px}
</style>
</head>
<body>

<header class="site-header">
  <div class="brand"><span class="brand-dot"></span>Brightmoor Talent</div>
  <nav class="main-nav">
    <a style="left:419px">Home</a>
    <a style="left:491px">About</a>
    <a style="left:576px">How it works</a>
    <a style="left:704px">Services</a>
    <a style="left:797px">Contact</a>
  </nav>
  <a class="btn" style="left:903px;top:29px;width:147px;height:61px">REGISTER</a>
  <a class="login-link">LOGIN</a>
</header>

<section class="hero" role="img" aria-label="Businessman holding a briefcase above a city skyline">
  <h1 class="hero-title">Welcome to <span>Brightmoor Talent</span></h1>
  <p class="hero-sub">Skilled workers from Sri Lanka, matched with<br>trusted employers right across Australia.</p>
  <a class="btn" style="left:518px;top:365px;width:172px;height:59px">UPLOAD RESUME</a>
  <span class="hero-arrow" style="left:32px"><svg width="34" height="34"><path d="M19 11 L12 17 L19 23Z" fill="#333"/></svg></span>
  <span class="hero-arrow" style="left:1132px"><svg width="34" height="34"><path d="M15 11 L22 17 L15 23Z" fill="#0b2a57"/></svg></span>
</section>

<section class="search-band">
  <div class="search-box">
    <span class="placeholder">Search For Job ⌄</span>
    <span class="go">SEARCH NOW</span>
  </div>
</section>

<h2 class="section-title" style="top:842px">SEARCH FOR JOB <span>VACANCY</span></h2>
<span class="tab active" style="left:297px">AGRICULTURE</span>
<span class="tab" style="left:518px">CONSTRUCTION</span>
<span class="tab" style="left:733px">PLUMBER</span>

<div class="job-card" style="left:141px;top:1028px"><div class="job-title">Electrician</div><p class="job-desc">Licensed trade role in Perth, WA. Visa sponsorship and relocation support.</p><a class="apply">Apply Now</a></div>
<div class="job-card alt" style="left:612px;top:1028px"><div class="job-title">Plumber</div><p class="job-desc">Residential plumbing in Brisbane, QLD. Full-time with skills assessment help.</p><a class="apply">Apply Now</a></div>
<div class="job-card" style="left:141px;top:1152px"><div class="job-title">Seller</div><p class="job-desc">Retail floor position in Adelaide, SA. Training and first-month housing given.</p><a class="apply">Apply Now</a></div>
<div class="job-card alt" style="left:612px;top:1152px"><div class="job-title">Sales Executive</div><p class="job-desc">B2B sales for a building supplier in Sydney. Base salary plus commission.</p><a class="apply dark">Apply Now</a></div>
<div class="job-card" style="left:141px;top:1278px"><div class="job-title">Manager</div><p class="job-desc">Site operations manager in Melbourne, VIC. Five years' experience needed.</p><a class="apply">Apply Now</a></div>
<div class="job-card alt" style="left:612px;top:1278px"><div class="job-title">Farmer</div><p class="job-desc">Dairy farm hand in regional Victoria. Seasonal contract with accommodation.</p><a class="apply">Apply Now</a></div>
<div class="job-card" style="left:141px;top:1404px"><div class="job-title">Marketing Executive</div><p class="job-desc">Brand and digital campaigns for a Gold Coast firm. Hybrid working offered.</p><a class="apply">Apply Now</a></div>
<div class="job-card alt" style="left:612px;top:1404px"><div class="job-title">Farmer</div><p class="job-desc">Horticulture worker in the Riverina, NSW. Harvest season, meals included.</p><a class="apply">Apply Now</a></div>

<span class="page-no" style="left:564px">1</span>
<span class="page-no" style="left:600px">2</span>
<span class="page-no current" style="left:637px">3</span>

<div class="about-ring"></div>
<div class="about-photo" role="img" aria-label="Recruiter shaking hands with a candidate in an office"></div>
<h2 class="about-title">ABOUT <span>US</span></h2>
<p class="about-text">Brightmoor Talent connects skilled Sri Lankan workers with Australian employers who need reliable people fast. We recruit electricians, plumbers, builders, farm hands and managers, then check every skill, reference and licence before a candidate is put forward. Our team in Colombo and Sydney guides each worker through skills assessment, visa lodgement, flights and arrival, while employers get one clear point of contact from first interview to first shift. Fair hiring, honest advice and long-term placements are at the heart of everything we do.</p>

<section class="how-band">
  <h2 class="section-title" style="top:63px">HOW IT <span>WORKS ?</span></h2>
  <svg class="abs" style="left:0;top:0" width="1200" height="400">
    <g fill="none" stroke="#b9c6d3" stroke-width="2" stroke-dasharray="7 6">
      <path d="M265 264 C320 250 350 245 385 252"/>
      <path d="M535 262 C580 275 610 290 650 300"/>
      <path d="M795 320 C850 318 880 300 915 290"/>
      <path d="M972 320 L972 340"/>
    </g>
  </svg>

  <div class="step-circle" style="left:118px;top:238px">
    <svg width="72" height="72" viewBox="0 0 72 72" fill="none" stroke="#0a2456" stroke-width="3"><rect x="8" y="10" width="56" height="38" rx="3"/><rect x="16" y="18" width="30" height="20" fill="#9ec0e6"/><path d="M30 48 L28 60 M42 48 L44 60 M22 60 H50"/><path d="M48 30 l8 10 -4 0 2 5 -3 1 -2 -5 -3 3z" fill="#fff"/></svg>
  </div>
  <span class="step-no" style="left:250px;top:359px">01</span>
  <div class="step-title" style="left:113px;top:425px">Submit Application</div>
  <p class="step-text" style="left:113px;top:463px">Upload your resume and trade papers online from anywhere in Sri Lanka.</p>

  <div class="step-circle" style="left:383px;top:161px">
    <svg width="72" height="72" viewBox="0 0 72 72" fill="none" stroke="#0a2456" stroke-width="3"><rect x="8" y="22" width="40" height="36" rx="3" fill="#9ec0e6"/><path d="M15 32 H40 M15 40 H40 M15 48 H32"/><path d="M44 30 V18 l6 -10 c4 0 4 4 3 8 h8 c3 0 4 3 3 6 l-3 10 H44z" fill="#fff"/></svg>
  </div>
  <span class="step-no" style="left:514px;top:282px">02</span>
  <div class="step-title" style="left:377px;top:348px">Review Application</div>
  <p class="step-text" style="left:377px;top:386px">We check your skills and call you back.</p>

  <div class="step-circle" style="left:646px;top:238px">
    <svg width="72" height="72" viewBox="0 0 72 72" fill="none" stroke="#0a2456" stroke-width="3"><path d="M36 6 L60 14 V34 C60 50 48 60 36 66 C24 60 12 50 12 34 V14Z" fill="#9ec0e6"/><circle cx="36" cy="36" r="13" fill="#fff"/><path d="M30 36 l5 5 9 -10"/></svg>
  </div>
  <span class="step-no" style="left:777px;top:359px">03</span>
  <div class="step-title" style="left:640px;top:425px">Join Suitable Job</div>
  <p class="step-text" style="left:640px;top:463px">Meet Australian employers by video, accept an offer and let us handle your visa paperwork.</p>

  <div class="step-circle" style="left:910px;top:161px">
    <svg width="72" height="72" viewBox="0 0 72 72" fill="none" stroke="#0a2456" stroke-width="3"><circle cx="44" cy="22" r="14" fill="#9ec0e6"/><path d="M48 16 h-6 a3 3 0 0 0 0 6 h4 a3 3 0 0 1 0 6 h-7 M44 12 v4 M44 28 v4"/><path d="M6 50 h12 l10 -6 h14 c3 0 3 5 0 5 h-10 M42 49 l16 -8 c3 -1 5 3 2 5 l-20 14 H18 M6 60 h12"/></svg>
  </div>
  <span class="step-no" style="left:1041px;top:282px">04</span>
  <div class="step-title" style="left:903px;top:348px">Start Earning</div>
  <p class="step-text" style="left:903px;top:386px">Fly to Australia with arrival support, settle into your new home and start earning a fair Australian wage, with our team on call from your very first day.</p>

  <a class="btn" style="left:543px;top:646px;width:147px;height:60px">READ MORE</a>
</section>

<h2 class="section-title" style="top:3028px">CLIENT <span>TESTIMONIALS</span></h2>
<span class="nav-circle" style="left:64px"><svg width="30" height="30"><path d="M17 10 L12 15 L17 20" fill="none" stroke="#999" stroke-width="2"/></svg></span>
<span class="nav-circle right" style="left:1102px"><svg width="30" height="30"><path d="M13 10 L18 15 L13 20" fill="none" stroke="#1a63b4" stroke-width="2"/></svg></span>
<article class="testimonial">
  <div class="client-photo"><div role="img" aria-label="Portrait of a smiling client"></div></div>
  <div class="client-name">Arjun Silva</div>
  <div class="client-role">CARPENTER, BRISBANE</div>
  <p class="client-quote">Brightmoor Talent found me a carpentry job in Brisbane within three months. They explained every visa step, met me at the airport and still check in with me today.</p>
  <svg class="quote-mark" width="54" height="44" viewBox="0 0 54 44" fill="#c3d3ea"><path d="M4 40 C4 24 10 12 22 6 L24 10 C16 16 14 22 16 26 C22 26 26 30 26 34 C26 40 21 44 15 44 C8 44 4 42 4 40Z"/><path d="M30 40 C30 24 36 12 48 6 L50 10 C42 16 40 22 42 26 C48 26 52 30 52 34 C52 40 47 44 41 44 C34 44 30 42 30 40Z"/></svg>
</article>

<footer class="site-footer">
  <a class="btn" style="left:391px;top:38px;width:152px;height:59px">REGISTER</a>
  <a class="btn" style="left:583px;top:38px;width:150px;height:59px">LOGIN</a>
  <span class="social" style="left:780px"></span>
  <span class="social" style="left:834px"></span>
  <div class="rule" style="top:144px"></div>
  <nav class="footer-links">Home<span>I</span>About<span>I</span>How it works<span>I</span>Services<span>I</span>Contact</nav>
  <div class="rule" style="top:208px"></div>
  <p class="copyright">©Copyrights 2022 Brightmoor Talent. All Rights Reserved.</p>
</footer>

</body>
</html>
```